need corporate, modern business card created for Consulting Company

I need a slick business card using elements from my website, as well as, integrating my pixelforge-created logo (see files).

The business card needs to be:
1. Corporate and modern
2. Clean and professional

I've included a PSD with the logo/icon that you can use to create it. Feel free to try a metallic finish on the logo, make it bigger/small, underlay it. Whatever you need to do to make my card stand out.

Try a black background, or white background or gray.

The idea is for my card to be memorable as well as professional and corporate.

Target Market(s)

Corporate business in the US and Canada.

Industry/Entity Type

Business

Contact Information for Business Card

Commerce Advancing Methods
Martin Coles, Senior Partner
office: 1 877 555 0143
mobile: 1 519 555 0172
website: http://www.brightvale.example

Requirements
Must have
• Card-related information
• corporate, yet modern
• clean and professional
• incorporate the icon only
• must have an editable form when complete!
Nice to have
• metallic icon might be cool
• try it with white or black

```html
<!DOCTYPE html>
<html lang="en">
<head>
<meta charset="utf-8">
<title>Brightvale Business Card</title>
<link href="https://fonts.googleapis.com/css2?family=Exo+2:wght@400;600&display=swap" rel="stylesheet">
<style>
  :root {
    --page: #e4e5e7;
    --card-black: #1d1d1f;
    --band-grey: #9ea3ab;
    --brand-blue: #3472c4;
    --text-white: #ffffff;
    --text-soft: #eef2f7;
  }
  * { margin: 0; padding: 0; box-sizing: border-box; }
  html, body { width: 1200px; height: 900px; overflow: hidden; }
  body {
    background: var(--page);
    font-family: "Exo 2", sans-serif;
    position: relative;
  }
  .card {
    position: absolute;
    left: 250px;
    width: 700px;
    height: 400px;
    border-radius: 30px;
    overflow: hidden;
    background: var(--card-black);
    box-shadow: 0 10px 28px rgba(0,0,0,0.22);
  }
  .card-front { top: 30px; }
  .card-back { top: 470px; }

  .accent-area {
    position: absolute;
    left: 0;
    top: 110px;
    width: 280px;
    height: 290px;
    background: linear-gradient(160deg, var(--brand-blue) 0%, var(--brand-blue) 60%, #5a7fae 100%);
  }

  .wordmark {
    position: absolute;
    display: flex;
    align-items: center;
    gap: 12px;
    color: var(--brand-blue);
    font-weight: 600;
    letter-spacing: 0.5px;
    line-height: 1;
  }
  .wordmark-square {
    width: 22px; height: 22px;
    background: var(--brand-blue);
  }
  .card-front .wordmark { left: 330px; top: 118px; font-size: 50px; }
  .card-back .wordmark { left: 225px; top: 170px; font-size: 60px; }
  .card-back .wordmark-square { width: 26px; height: 26px; }

  .holder {
    position: absolute;
    right: 90px;
    top: 222px;
    text-align: right;
    color: var(--text-white);
  }
  .holder-name {
    font-size: 21px;
    font-weight: 600;
    letter-spacing: 2px;
    text-transform: uppercase;
  }
  .holder-role {
    font-size: 16px;
    font-weight: 400;
    letter-spacing: 0.8px;
    margin-top: 2px;
  }

  .contact-list {
    position: absolute;
    left: 22px;
    top: 178px;
    list-style: none;
    color: var(--text-soft);
    font-size: 11.5px;
    font-weight: 400;
  }
  .contact-item {
    display: flex;
    align-items: center;
    gap: 7px;
    height: 25px;
    white-space: nowrap;
  }
  .contact-icon { width: 15px; height: 15px; flex: none; }
</style>
</head>
<body>

  <section class="card card-front" aria-label="Business card front">
    <div class="accent-area" role="img" aria-label="Decorative wave band in blue and grey"></div>

    <div class="wordmark"><span class="wordmark-square"></span>brightvale</div>

    <div class="holder">
      <p class="holder-name">Martin Coles</p>
      <p class="holder-role">Managing Director</p>
    </div>

    <ul class="contact-list">
      <li class="contact-item">
        <svg class="contact-icon" viewBox="0 0 16 16"><circle cx="8" cy="8" r="8" fill="#fff"/><path d="M5.2 4.2l1.5-.4.9 2-1 .8c.5 1.1 1.3 1.9 2.4 2.4l.8-1 2 .9-.4 1.5c-3.3.2-6.4-2.9-6.2-6.2z" fill="var(--brand-blue)"/></svg>
        <span>1 877 555 0143</span>
      </li>
      <li class="contact-item">
        <svg class="contact-icon" viewBox="0 0 16 16"><circle cx="8" cy="8" r="8" fill="#fff"/><rect x="5.5" y="3.5" width="5" height="9" rx="1" fill="var(--brand-blue)"/><rect x="6.5" y="4.8" width="3" height="5.2" fill="#fff"/></svg>
        <span>1 519 555 0172</span>
      </li>
      <li class="contact-item">
        <svg class="contact-icon" viewBox="0 0 16 16"><circle cx="8" cy="8" r="8" fill="#fff"/><rect x="4" y="5" width="8" height="6" fill="var(--brand-blue)"/><path d="M4 5l4 3.2L12 5" stroke="#fff" stroke-width="0.9" fill="none"/></svg>
        <span>martin@brightvale.example</span>
      </li>
      <li class="contact-item">
        <svg class="contact-icon" viewBox="0 0 16 16"><circle cx="8" cy="8" r="8" fill="#fff"/><circle cx="8" cy="8" r="4.2" stroke="var(--brand-blue)" stroke-width="1" fill="none"/><path d="M3.8 8h8.4M8 3.8c-2 2.4-2 6 0 8.4M8 3.8c2 2.4 2 6 0 8.4" stroke="var(--brand-blue)" stroke-width="0.8" fill="none"/></svg>
        <span>www.brightvale.example</span>
      </li>
      <li class="contact-item">
        <svg class="contact-icon" viewBox="0 0 16 16"><circle cx="8" cy="8" r="8" fill="#fff"/><path d="M8 12.5s-3-3.3-3-5.4a3 3 0 016 0c0 2.1-3 5.4-3 5.4z" fill="var(--brand-blue)"/><circle cx="8" cy="7" r="1.1" fill="#fff"/></svg>
        <span>41 Harbour Crest Road</span>
      </li>
    </ul>
  </section>

  <section class="card card-back" aria-label="Business card back">
    <div class="wordmark"><span class="wordmark-square"></span>brightvale</div>
  </section>

</body>
</html>
```